Verdanith Website Concept

We would like a one page website. Please refer to the attached files for more information.

Please reference file attachment version 1.1.

```html
<!DOCTYPE html>
<html lang="en">
<head>
<meta charset="utf-8">
<title>Verdanith — Tier One Security</title>
<link href="https://fonts.googleapis.com/css2?family=PT+Sans:wght@400;700&display=swap" rel="stylesheet">
<style>
:root{
  --sky:#6ab8e0;
  --sky-dark:#58a7d2;
  --navy:#2f3b78;
  --ink:#333;
  --muted:#8a8a8a;
  --hero-bg:#e8ebee;
  --section-bg:#f5f5f5;
  --line:#e2e2e2;
  --footer:#363636;
}
*{margin:0;padding:0;box-sizing:border-box}
html,body{width:785px;height:1200px;overflow:hidden}
body{position:relative;background:#fff;font-family:"PT Sans",sans-serif;color:var(--ink)}
.abs{position:absolute}
.topbar{left:0;top:0;width:785px;height:2.4px;background:var(--sky)}
.header{left:0;top:2.4px;width:785px;height:66.6px;background:#fff;border-bottom:1px solid #ddd}
.brand{left:86px;top:22px;display:flex;align-items:center;gap:6px;font-size:17px;color:var(--navy);letter-spacing:1px}
.brand-mark{width:30px;height:30px;border-radius:50%;background:var(--navy)}
.nav a{position:absolute;top:26px;height:26px;line-height:26px;font-size:9.5px;color:#555;text-decoration:none}
.nav .active{left:330px;width:54px;text-align:center;background:var(--sky);color:#fff}
.hero{left:0;top:69px;width:785px;height:357px;background:linear-gradient(135deg,#eceef1,#e2e6ea)}
.hero-card{left:86px;top:107px;width:613px;height:280px;background:#fff;box-shadow:0 1px 3px rgba(0,0,0,.08)}
.hero-kicker{left:118px;top:150px;font-size:21px;font-weight:700;color:var(--navy)}
.hero-title{left:118px;top:191px;font-size:22px;font-weight:700;color:var(--sky)}
.hero-sub{left:118px;top:222px;font-size:14px;color:#444}
.hero-text{left:120px;top:254px;width:300px;font-size:9.6px;line-height:15px;color:#777}
.btn-read{left:122px;top:314px;width:80px;height:32px;line-height:32px;text-align:center;background:var(--sky);color:#fff;font-size:9.5px;font-weight:700}
.hero-photo{left:452px;top:107px;width:212px;height:280px;background:linear-gradient(180deg,#d9c1ad,#6b6a74 60%,#54535c)}
.welcome{left:0;top:426px;width:785px;height:502px;background:var(--section-bg)}
.h2{font-size:14.5px;font-weight:700;color:#2a2a2a}
.h2 span{color:var(--sky)}
.welcome-title{left:0;width:785px;top:452px;text-align:center}
.welcome-text{left:86px;top:486px;width:613px;text-align:center;font-size:7.9px;line-height:13.4px;color:#888}
.rule{height:1px;background:var(--line)}
.form{left:86px;top:584px;width:167px;height:312px;background:var(--sky)}
.form-title{left:86px;top:594px;width:167px;text-align:center;font-size:11px;font-weight:700;color:#fff}
.form-sep{left:86px;top:614px;width:167px;height:1px;background:#8ccbea}
.field{position:absolute;background:#fff;border:1px solid #9fd1ea;font-size:6.8px;color:#999;padding:3px 4px}
.select::after{content:"";position:absolute;right:4px;top:7px;border:2.5px solid transparent;border-top:3px solid #999}
.select::before{content:"";position:absolute;right:11px;top:3px;width:1px;height:11px;background:#ccc}
.form-btn{left:94px;top:862px;width:149px;height:26px;line-height:26px;text-align:center;background:var(--sky-dark);border:1px solid #4f9ac4;color:#fff;font-size:8px;font-weight:700}
.svc-title{left:290px;top:579px}
.svc-intro{left:290px;top:627px;width:410px;font-size:6.5px;line-height:16px;color:#888;text-transform:uppercase}
.svc-icon{position:absolute;width:48px;height:62px;border-radius:6px}
.svc-name{position:absolute;font-size:13.5px;line-height:17px;color:var(--navy)}
.svc-desc{position:absolute;width:135px;font-size:7.8px;line-height:12px;color:#999}
.news-title{left:0;width:785px;top:948px;text-align:center}
.news-arrow{top:951px;width:13px;height:13px;border-radius:50%}
.news-img{position:absolute;top:990px;width:115px;height:107px;border:1px solid #ddd}
.news-head{position:absolute;top:998px;font-size:9px;font-weight:700;color:var(--sky)}
.news-date{position:absolute;top:1009px;font-size:8.5px;color:#222}
.news-date b{margin-left:8px}
.news-text{position:absolute;top:1029px;width:145px;font-size:7px;line-height:11px;color:#888}
.news-more{position:absolute;top:1082px;width:46px;height:17px;line-height:17px;text-align:center;background:#555;color:#fff;font-size:7px;font-weight:700}
.footline{left:0;top:1142px;width:785px;height:2.4px;background:var(--sky)}
.footer{left:0;top:1144px;width:785px;height:56px;background:var(--footer)}
.foot-text{top:1166px;font-size:6.8px;color:#ddd}
.social{top:1165px;width:14px;height:14px;border-radius:50%;border:1.5px solid #fff}
</style>
</head>
<body>
<div class="abs topbar"></div>
<header class="abs header"></header>
<div class="abs brand"><span class="brand-mark"></span>VERDANITH</div>
<nav class="nav">
  <a class="active">HOME</a>
  <a style="left:402px">ABOUT</a>
  <a style="left:461px">SERVICES »</a>
  <a style="left:532px">PROJECTS »</a>
  <a style="left:606px">BLOG</a>
  <a style="left:654px">CONTACTS</a>
</nav>

<section class="abs hero"></section>
<svg class="abs" style="left:50px;top:220px" width="30" height="54"><polyline points="26,2 3,27 26,52" fill="none" stroke="#b9bec4" stroke-width="1.5"/></svg>
<svg class="abs" style="left:705px;top:220px" width="30" height="54"><polyline points="4,2 27,27 4,52" fill="none" stroke="#b9bec4" stroke-width="1.5"/></svg>
<div class="abs hero-card"></div>
<div class="abs hero-kicker">VERDANITH</div>
<div class="abs hero-title">UNITED STATES-BASED</div>
<div class="abs hero-sub">TIER ONE SECURITY FIRM SPECIALIZING</div>
<p class="abs hero-text">To create a single page website that clearly stands out among all other elite security company websites and reflects the essence of Verdanith's mission and appeals to it's executive clientele</p>
<div class="abs btn-read">READ MORE</div>
<div class="abs hero-photo" role="img" aria-label="Portrait of a smiling executive in a grey suit, arms crossed"></div>

<section class="abs welcome"></section>
<h2 class="abs h2 welcome-title"><span>WELCOME</span> TO OUR COMPANY</h2>
<p class="abs welcome-text">Verdanith is a United States-based tier one security firm specializing in the protection of financial services professionals, executives and their families. We manage engagements resulting from general and specific threats throughout the United States and abroad on behalf of our domestic clients. We deliver our services exclusively through associates and contractors with United States special operations, secret service, Halvern Agency, or equivalent experience and training. We are one of only a handful of domestic security firms that offers scalable, tier one security services in every market in the United States.</p>
<div class="abs rule" style="left:86px;top:564px;width:613px"></div>

<div class="abs form"></div>
<div class="abs form-title">REQUEST A CONSULTATION</div>
<div class="abs form-sep"></div>
<div class="field" style="left:94px;top:626px;width:72px;height:19px">First Name</div>
<div class="field" style="left:173px;top:626px;width:70px;height:19px">Last Name</div>
<div class="field" style="left:94px;top:651px;width:72px;height:19px">Home Phone</div>
<div class="field" style="left:173px;top:651px;width:70px;height:19px">Work Phone</div>
<div class="field" style="left:94px;top:677px;width:149px;height:18px">Cell Phone</div>
<div class="field" style="left:94px;top:702px;width:149px;height:18px">Email Address</div>
<div class="field" style="left:94px;top:727px;width:72px;height:46px">Address</div>
<div class="field" style="left:173px;top:727px;width:70px;height:46px">Address</div>
<div class="field select" style="left:94px;top:781px;width:48px;height:18px">City</div>
<div class="field select" style="left:145px;top:781px;width:47px;height:18px">State</div>
<div class="field" style="left:195px;top:781px;width:48px;height:18px">Zip</div>
<div class="field" style="left:94px;top:806px;width:149px;height:46px">Message</div>
<div class="abs form-btn">EQUEST FOR CONSULTATION</div>

<h2 class="abs h2 svc-title"><span>SERVICE</span>&nbsp; OFFERINGS</h2>
<div class="abs rule" style="left:290px;top:611px;width:398px"></div>
<p class="abs svc-intro">Our firm was created as the result of a specific threat to two of our founders resulting from a private equity transaction with a hostile seller. If you are a transaction professional</p>

<div class="svc-icon" style="left:290px;top:684px;background:radial-gradient(circle at 50% 40%,#f3b23a,#3a8fd0 55%,transparent 70%)" role="img" aria-label="Globe icon"></div>
<div class="svc-name" style="left:348px;top:682px">Threat Assessment</div>
<p class="svc-desc" style="left:348px;top:724px">At vero eos et accusamuset iusto odioi ssimosducimus qui.At vero eos et accn et iusto odio dignissimosxfhf</p>

<div class="svc-icon" style="left:510px;top:684px;background:linear-gradient(180deg,#5a6e86,#cfd6de)" role="img" aria-label="Laptop with chart icon"></div>
<div class="svc-name" style="left:566px;top:682px">Threat Avoidance Plan<br>&amp; Dossier Creation</div>
<p class="svc-desc" style="left:567px;top:726px">At vero eos et accusamuset iusto odioi ssimosducimus qui.At vero eos et accn et iusto odio dignissimosxfhf</p>

<div class="svc-icon" style="left:290px;top:792px;background:radial-gradient(circle at 50% 50%,#f29a74,#f7c6ad 60%,transparent 72%)" role="img" aria-label="Piggy bank icon"></div>
<div class="svc-name" style="left:348px;top:791px">Elite Executive<br>Protection</div>
<p class="svc-desc" style="left:348px;top:833px">At vero eos et accusamuset iusto odioi ssimosducimus qui.At vero eos et accn et iusto odio dignissimosxfhf</p>

<div class="svc-icon" style="left:510px;top:792px;background:linear-gradient(180deg,#8cc74a,#e1b83e)" role="img" aria-label="Gold coin stacks with rising arrow icon"></div>
<div class="svc-name" style="left:566px;top:791px">Threat Avoidance Plan<br>&amp; Dossier Maintenance</div>
<p class="svc-desc" style="left:567px;top:833px">At vero eos et accusamuset iusto odioi ssimosducimus qui.At vero eos et accn et iusto odio dignissimosxfhf</p>
<div class="abs rule" style="left:290px;top:898px;width:398px"></div>

<svg class="abs news-arrow" style="left:322px" viewBox="0 0 13 13"><circle cx="6.5" cy="6.5" r="6.5" fill="#c8c8c8"/><polyline points="7.8,3.5 4.8,6.5 7.8,9.5" fill="none" stroke="#fff" stroke-width="1.6"/></svg>
<h2 class="abs h2 news-title"><span>LATEST</span> NEWS</h2>
<svg class="abs news-arrow" style="left:446px" viewBox="0 0 13 13"><circle cx="6.5" cy="6.5" r="6.5" fill="#777"/><polyline points="5.2,3.5 8.2,6.5 5.2,9.5" fill="none" stroke="#fff" stroke-width="1.6"/></svg>

<div class="news-img" style="left:86px;background:linear-gradient(135deg,#e9e4df,#c9b59d 50%,#eef0f2)" role="img" aria-label="Photo of colleagues working at a desk"></div>
<div class="news-head" style="left:223px">Lorem ipsum dolore</div>
<div class="news-date" style="left:223px">massa laoreetum <b>14 &nbsp;MAR</b></div>
<p class="news-text" style="left:223px">Phasellus porta. Fusce susct varius mi. Cum sociis natoque penabus et magnis dis parturient montes, nascetur ridiculus mus. Nulla dui. Fusce feugiat malesuada odio</p>
<div class="news-more" style="left:224px">MORE</div>
<div class="abs" style="left:394px;top:1000px;width:1px;height:88px;background:#e6e6e6"></div>
<div class="news-img" style="left:422px;background:radial-gradient(circle at 50% 40%,#7c9a6a,#cfd8c5 60%,#f2f2f2)" role="img" aria-label="Photo of a tree growing banknotes"></div>
<div class="news-head" style="left:559px">Lorem ipsum dolore</div>
<div class="news-date" style="left:559px">massa laoreetum <b>14 &nbsp;MAR</b></div>
<p class="news-text" style="left:559px">Phasellus porta. Fusce susct varius mi. Cum sociis natoque penabus et magnis dis parturient montes, nascetur ridiculus mus. Nulla dui. Fusce feugiat malesuada odio</p>
<div class="news-more" style="left:560px">MORE</div>

<div class="abs footline"></div>
<footer class="abs footer"></footer>
<div class="abs foot-text" style="left:85px">REFERENCES AVAILABLE UPON REQUEST</div>
<div class="abs foot-text" style="left:329px">(c) 2014 All rights reserved Verdanith, LLC</div>
<div class="abs social" style="left:587px;background:#c9302c"></div>
<div class="abs social" style="left:606px;background:#2a9fd6"></div>
<div class="abs social" style="left:625px;background:#3b5998"></div>
<div class="abs social" style="left:644px;background:#d6492f"></div>
<div class="abs social" style="left:663px;background:#f26522"></div>
<div class="abs social" style="left:682px;background:#2b7bb9"></div>
</body>
</html>
```